Industry automation wholesale website

www.velturo.eu provides solutions for automation, building automation and digital signage.

Our products are rugged, reliable, energy saving and representative.

Scope of pages:
● welcome page
- scope of products
- applications, success stories and news
● category page
- short introduction
- sub categories
- product highlights
● product page
- short introduction
- about 3 to 4 pictures
- technical specifications: materials, dimensions
- price
- related products

Optional:
● contact page
- address
- contact form
● blog
- picture
- text
● logo
● favicon / apple touch icon

Conclusion:
● We need a professionally looking site
● Bright colors (e.g. white, grey, metalic colors, blue)

some pages we like:
http://www.prandek.de/
http://www.morvalix.de/

Target Market(s)

Our target market is the industrial sector
● Target audience: engineering and IT professionals

Industry/Entity Type

Building

Requirements
Must have
• ● only use free available fonts e.g. Lumara Type Library (http://www.lumaratype.com/webfonts)
Should not have
• ● sound
● flash

```html
<!DOCTYPE html>
<html lang="en">
<head>
<meta charset="utf-8">
<title>velturo – industrial automation</title>
<link href="https://fonts.googleapis.com/css2?family=Open+Sans:wght@400;600;700&display=swap" rel="stylesheet">
<style>
:root{
  --page:#efefef;
  --white:#ffffff;
  --bar:#6a6a6a;
  --bar-dark:#454545;
  --blue:#1b79ad;
  --blue-dark:#135f8a;
  --title:#1d6c98;
  --text:#2b2b2b;
  --ink:#3a3a3a;
  --line:#dcdcdc;
  --card-head:#5d5d5d;
  --foot-a:#2b9ed4;
  --foot-b:#17649f;
}
*{box-sizing:border-box;margin:0;padding:0}
html,body{width:1090px;height:1200px;overflow:hidden;background:var(--page);font-family:"Open Sans",Arial,sans-serif;color:var(--text)}
.canvas{width:1090px;height:1200px;overflow:hidden;position:relative}
.stage{position:absolute;left:0;top:0;width:1170px;height:1288px;transform:scale(.93162);transform-origin:0 0}
.page{position:absolute;left:75px;top:0;width:1020px;height:1288px;background:var(--white)}
.abs{position:absolute}
/* top bar */
.topbar{left:0;top:0;width:1020px;height:25px;background:var(--bar);color:#fff;font-size:13px;font-weight:600}
.topbar .item{position:absolute;top:3px;display:flex;align-items:center;gap:6px;white-space:nowrap}
.topbar .ico{width:19px;height:19px;border:1.5px solid #fff;border-radius:50%;display:inline-block}
.lang{position:absolute;right:0;top:0;width:106px;height:25px;background:var(--bar-dark);font-weight:400;font-size:12px;padding:4px 0 0 13px;white-space:nowrap}
.lang i{display:inline-block;width:18px;height:11px;background:linear-gradient(#c8102e 0 0) center/100% 3px no-repeat,linear-gradient(#c8102e 0 0) center/3px 100% no-repeat,#1c3c8c;margin-left:8px;vertical-align:-1px}
/* header */
.header{left:0;top:25px;width:1020px;height:100px;background:linear-gradient(#eaf4fa,#fff 40%)}
.brand{left:20px;top:34px;display:flex;align-items:center;gap:12px}
.brand .mark{width:22px;height:22px;background:var(--blue)}
.brand .name{font-size:40px;font-weight:600;color:var(--ink);line-height:44px}
.cart{left:602px;top:26px;font-size:13px;display:flex;gap:6px;align-items:center;white-space:nowrap}
.search{left:801px;top:20px;width:200px;height:27px;border:1px solid #d3d3d3;border-radius:3px;font-size:13px;color:#999;padding:4px 11px}
.search svg{position:absolute;right:8px;top:5px}
.nav{right:19px;top:64px;display:flex;font-size:14px;white-space:nowrap}
.nav a{color:#222;text-decoration:none;padding:3px 11px;margin-left:3px;height:24px}
.nav a:last-child{padding-right:0}
.nav a.active{background:var(--blue);color:#fff;border-radius:2px}
/* hero */
.hero{left:20px;top:133px;width:981px;height:362px}
.hero .title{position:absolute;left:537px;top:66px;font-size:27px;font-weight:600;color:var(--title);white-space:nowrap}
.hero dl{position:absolute;left:539px;top:122px;font-size:16px}
.hero dt{font-weight:700;color:#111}
.hero dd{margin-bottom:9px;color:#222}
.btn{display:inline-block;background:linear-gradient(#2790c6,var(--blue-dark));color:#fff;border-radius:3px;border-bottom:3px solid #0d4a6e;text-decoration:none;white-space:nowrap}
.hero .btn{position:absolute;left:540px;top:289px;width:134px;height:39px;font-size:15px;text-align:center;line-height:36px}
.new{position:absolute;left:28px;top:57px;width:86px;height:86px;border-radius:50%;background:#e2231a;color:#fff;font-weight:700;font-size:22px;text-align:center;line-height:86px}
/* cards */
.card{top:525px;width:231px;height:318px;border:1px solid #ddd;border-top:0;box-shadow:0 1px 3px rgba(0,0,0,.15);background:#fff}
.card h3{height:35px;background:linear-gradient(#777,var(--card-head));color:#fff;font-size:15px;font-weight:600;padding:8px 16px;text-transform:uppercase;white-space:nowrap}
.card ul{list-style:none;padding:4px 18px 0 18px}
.card li{height:30px;border-bottom:1px solid var(--line);font-size:12.5px;display:flex;justify-content:space-between;align-items:center}
.card li:last-child{border-bottom:0}
.card li b{width:11px;height:11px;border:1px solid #bbb;font-size:10px;line-height:8px;text-align:center;color:#999;font-weight:400}
.card .photo{margin:13px 0 0 15px;width:200px;height:150px}
.card p{font-size:11.8px;line-height:22px;padding:9px 12px 0 15px;color:#222;letter-spacing:-.1px}
.card .btn,.small-btn{font-size:11.5px;font-weight:600;padding:2px 13px;border-bottom-width:2px}
.card .btn{margin:5px 0 0 16px}
/* lists */
.section-title{font-size:15px;font-weight:600;text-transform:uppercase;color:#111}
.entry{position:absolute;height:70px;border-bottom:1px solid var(--line)}
.entry h4{font-size:13px;font-weight:600;color:var(--blue);margin-bottom:1px;white-space:nowrap}
.entry p{font-size:11px;line-height:20px;color:#333;letter-spacing:-.1px}
.date{position:absolute;left:0;top:0;width:46px;text-align:center}
.date .m{background:#d6d6d6;font-size:12px;height:23px;line-height:23px}
.date .d{background:var(--blue-dark);color:#fff;font-weight:700;font-size:15px;height:25px;line-height:24px}
.thumb{position:absolute;left:0;top:0;width:67px;height:50px;background:linear-gradient(#9cc4df,#dbe9f2)}
/* footer */
.footer{left:0;top:1174px;width:1020px;height:114px;background:linear-gradient(var(--foot-a),var(--foot-b));color:#fff}
.footer .links{position:absolute;left:19px;top:24px;font-size:12.5px;white-space:nowrap}
.footer .links span{margin:0 8px;opacity:.8}
.footer .copy{position:absolute;left:19px;top:49px;font-size:12.5px}
.footer .legal{position:absolute;left:19px;top:75px;font-size:11px;opacity:.85}
.footer .follow{position:absolute;right:21px;top:24px;font-size:12.5px}
.social{position:absolute;top:57px;width:34px;height:34px;border-radius:50%;box-shadow:0 2px 3px rgba(0,0,0,.3)}
</style>
</head>
<body>
<div class="canvas"><div class="stage"><div class="page">

  <div class="abs topbar">
    <div class="item" style="left:615px"><span class="ico"></span>info@velturo.de</div>
    <div class="item" style="left:763px"><span class="ico"></span>+49-211-5550123</div>
    <div class="lang">Language<i></i></div>
  </div>

  <header class="abs header">
    <div class="abs brand"><span class="mark"></span><span class="name">velturo</span></div>
    <div class="abs cart">
      <svg width="15" height="13" viewBox="0 0 15 13"><path d="M0 1h3l2 7h8l2-5H4" fill="none" stroke="#1b79ad" stroke-width="1.5"/><circle cx="6" cy="11" r="1.3" fill="#1b79ad"/><circle cx="12" cy="11" r="1.3" fill="#1b79ad"/></svg>
      Products:0 Price: $0.00
    </div>
    <div class="abs search">Product search
      <svg width="16" height="16" viewBox="0 0 16 16"><circle cx="6.5" cy="6.5" r="5" fill="none" stroke="#999" stroke-width="1.5"/><path d="M10 10l5 5" stroke="#999" stroke-width="1.5"/></svg>
    </div>
    <nav class="abs nav"><a class="active">HOME</a><a>ABOUT US</a><a>PRODUCTS</a><a>BLOG</a><a>CONTACT US</a></nav>
  </header>

  <section class="abs hero">
    <svg width="981" height="362" style="position:absolute;left:0;top:0">
      <defs>
        <linearGradient id="heroFill" x1="0" y1="0" x2="1" y2="0.3">
          <stop offset="0" stop-color="#5fb3e0"/><stop offset=".45" stop-color="#c9e6f5"/><stop offset="1" stop-color="#9ed1ec"/>
        </linearGradient>
      </defs>
      <path d="M0 20 Q490 -20 981 20 L981 340 Q490 380 0 340 Z" fill="url(#heroFill)"/>
      <circle cx="34" cy="184" r="15" fill="none" stroke="#fff" stroke-width="2"/>
      <path d="M37 177l-7 7 7 7" fill="none" stroke="#fff" stroke-width="2"/>
      <circle cx="947" cy="184" r="15" fill="none" stroke="#fff" stroke-width="2"/>
      <path d="M944 177l7 7-7 7" fill="none" stroke="#fff" stroke-width="2"/>
    </svg>
    <div role="img" aria-label="Photo of an industrial touch panel PC" style="position:absolute;left:100px;top:30px;width:250px;height:300px;background:linear-gradient(135deg,#1a1a1a,#1d4fb0 40%,#3a8de0 70%,#1a1a1a);transform:skewY(-5deg);border-radius:4px"></div>
    <div class="new">NEW</div>
    <div class="title">Touch Panel PC/Bedienterminal</div>
    <dl>
      <dt>Industrial</dt><dd>IP65 Front 24/7 continous operation</dd>
      <dt>Performance</dt><dd>Corvex Dual Core C525 1,8 GHz</dd>
      <dt>Fanless</dt><dd>Low heat emission, power saving</dd>
    </dl>
    <a class="btn">View Details</a>
  </section>

  <section class="abs card" style="left:20px">
    <h3>Range of Products</h3>
    <ul>
      <li>RS422 / RS485 Converter<b>+</b></li>
      <li>RS422 / RS485 Repeater<b>+</b></li>
      <li>Embedded Systems<b>+</b></li>
      <li>RS485 Remote IO<b>+</b></li>
      <li>RS485 Modbus IO<b>+</b></li>
      <li>Embedded Systems<b>+</b></li>
      <li>PCI-Series<b>+</b></li>
      <li>Industry PC<b>+</b></li>
      <li>Industrial Display<b>+</b></li>
    </ul>
  </section>
  <section class="abs card" style="left:270px">
    <h3>Modbus RTU / RS485</h3>
    <div class="photo" role="img" aria-label="Photo of RS485 remote IO modules on a rail" style="background:linear-gradient(135deg,#4a88c6,#b7d4ec 50%,#3c77b4)"></div>
    <p>RS485 Remote IO modules are ideal to realize decentralized distributed IO units over long distances.</p>
    <a class="btn">View Details</a>
  </section>
  <section class="abs card" style="left:521px">
    <h3>Touch Panel Industry</h3>
    <div class="photo" role="img" aria-label="Photo of an industrial touch panel" style="background:linear-gradient(135deg,#c9c9c9,#8e959c 30%,#4f8fd8 55%,#9aa0a6)"></div>
    <p>RS485 Remote IO modules are ideal to realize decentralized distributed IO units over long distances.</p>
    <a class="btn">View Details</a>
  </section>
  <section class="abs card" style="left:771px">
    <h3>Embedded Systems</h3>
    <div class="photo" role="img" aria-label="Photo of a fanless embedded box PC" style="background:linear-gradient(160deg,#7fb3df,#2d3136 55%,#6ea6d8)"></div>
    <p>RS485 Remote IO modules are ideal to realize decentralized distributed IO units over long distances.</p>
    <a class="btn">View Details</a>
  </section>

  <section class="abs" style="left:20px;top:869px;width:495px;height:270px">
    <h2 class="section-title">Latest News</h2>
    <div class="entry" style="left:0;top:33px;width:495px"><div class="date"><div class="m">Jan</div><div class="d">03</div></div><div style="margin-left:60px"><h4>Lorem Ipsum is simply</h4><p>Lorem Ipsum is simply dummy text of the printing and typesetting industry. Lorem Ipsum has been the industry</p></div></div>
    <div class="entry" style="left:0;top:105px;width:495px"><div class="date"><div class="m">Jan</div><div class="d">03</div></div><div style="margin-left:60px"><h4>Lorem Ipsum is simply</h4><p>Lorem Ipsum is simply dummy text of the printing and typesetting industry. Lorem Ipsum has been the industry</p></div></div>
    <div class="entry" style="left:0;top:175px;width:495px;border:0"><div class="date"><div class="m">Jan</div><div class="d">03</div></div><div style="margin-left:60px"><h4>Lorem Ipsum is simply</h4><p>Lorem Ipsum is simply dummy text of the printing and typesetting industry. Lorem Ipsum has been the industry</p></div></div>
    <a class="btn small-btn abs" style="left:0;top:241px">View All News</a>
  </section>

  <section class="abs" style="left:556px;top:869px;width:432px;height:270px">
    <h2 class="section-title">Success Stories</h2>
    <div class="entry" style="left:0;top:29px;width:432px"><div class="thumb" role="img" aria-label="Photo for customer story"></div><div style="margin-left:81px"><h4>Lorem Ipsum is simply</h4><p>Lorem Ipsum is simply dummy text of the printing and typesetting industry. Lorem Ipsum has been the industry</p></div></div>
    <div class="entry" style="left:0;top:101px;width:432px"><div class="thumb" role="img" aria-label="Photo for customer story"></div><div style="margin-left:81px"><h4>Lorem Ipsum is simply</h4><p>Lorem Ipsum is simply dummy text of the printing and typesetting industry. Lorem Ipsum has been the industry</p></div></div>
    <div class="entry" style="left:0;top:171px;width:432px;border:0"><div class="thumb" role="img" aria-label="Photo for customer story"></div><div style="margin-left:81px"><h4>Lorem Ipsum is simply</h4><p>Lorem Ipsum is simply dummy text of the printing and typesetting industry. Lorem Ipsum has been the industry</p></div></div>
    <a class="btn small-btn abs" style="left:1px;top:241px;padding:2px 20px">View All</a>
  </section>

  <footer class="abs footer">
    <div class="links">Home<span>|</span>About Us<span>|</span>Products<span>|</span>Blog<span>|</span>Contact Us</div>
    <div class="copy">Copyright © 2014 velturo.eu. All Rights Reserved.</div>
    <div class="legal">Terms &amp; Conditions <span style="margin:0 8px">|</span> Masthead</div>
    <div class="follow">Follow Us</div>
    <span class="social" aria-label="Social profile" style="left:887px;background:#3b5a9a"></span>
    <span class="social" aria-label="Social profile" style="left:928px;background:#2aa6de"></span>
    <span class="social" aria-label="Social profile" style="left:968px;background:#cf3f2e"></span>
  </footer>

</div></div></div>
</body>
</html>
```